Bright Harbor Charity - helping the disadvantaged

I would like a new web site design for my charity BRIGHT HARBOR. The charity provides help for the disadvantaged. See current site
brightharbor.org.au for details. Please refer to the current site for information on the charity. The objectives of the charity are in the "about us" tab. You will also notice on the site that we provide information about events that we sponsor an area for this should be provided on the site.

Target Market(s)

We have two targets:
1. Individuals and Businesses that will donate money to the charity.
2. Individuals that are in need of support from the charity.

Industry/Entity Type

Charity

Requirements
Must have
• Ability for individuals to be able to understand the type of support we can provide.
Nice to have
• Our logo should be prominate on each pages
Should not have
• Should be use modern fonts

```html
<!DOCTYPE html>
<html lang="en">
<head>
<meta charset="utf-8">
<title>Bright Harbor</title>
<link rel="stylesheet" href="https://fonts.googleapis.com/css2?family=Arimo:wght@400;700&display=swap">
<style>
:root{
  --page-bg:#f4f4f3;
  --panel:#ffffff;
  --content-bg:#f5f3f4;
  --line:#c9c9c9;
  --nav:#3a3a3a;
  --nav-dark:#121212;
  --footer:#454545;
  --brand-green:#4a9a3a;
  --accent-red:#7c0d0d;
  --register:#a23a3a;
  --text:#1a1a1a;
  --muted:#d0d0d0;
  --heading:#444;
}
*{box-sizing:border-box;margin:0;padding:0}
html,body{width:1200px;height:1052px;overflow:hidden}
body{background:var(--page-bg);font-family:"Arimo",Arial,sans-serif;color:var(--text);position:relative}
.abs{position:absolute}
.page{left:125px;top:0;width:948px;height:1017px;background:linear-gradient(#f1f1f1,#fff 130px);box-shadow:0 0 14px rgba(0,0,0,.35);border-radius:0 0 16px 16px}
.logo{left:168px;top:38px;font-size:44px;font-weight:400;color:var(--brand-green);letter-spacing:1px;display:flex;align-items:center;gap:12px}
.logo .mark{width:16px;height:16px;border-radius:50%;background:var(--brand-green)}
.btn-login{left:776px;top:0;width:105px;height:29px;background:#2f2f2f;color:#fff;font-weight:700;font-size:15px;display:flex;align-items:center;justify-content:center;border-radius:0 0 4px 4px}
.btn-register{left:886px;top:0;width:105px;height:40px;background:var(--register);color:#fff;font-weight:700;font-size:15px;display:flex;align-items:center;justify-content:center;border-radius:0 0 4px 4px}
.nav{left:112px;width:974px;display:flex;justify-content:center;align-items:center;color:#fff;font-weight:700}
.nav span.sep{margin:0 20px}
.nav-main{top:130px;height:55px;background:var(--nav);font-size:15px;box-shadow:0 2px 4px rgba(0,0,0,.3)}
.nav-foot{top:844px;height:56px;background:var(--nav-dark);font-size:13px}
.nav-foot span.sep{margin:0 17px}
.footer{left:125px;top:900px;width:948px;height:117px;background:var(--footer);border-radius:0 0 16px 16px}
.copyright{left:34px;top:50px;font-size:10.5px;line-height:18px;color:var(--muted);font-weight:700}
.social{top:36px;height:40px;display:flex;align-items:center;justify-content:center;font-size:12px;font-weight:700;border-radius:3px}
.social.chatter{left:684px;width:74px;background:#efe6cf;color:#3a7aa8}
.social.friendbook{left:784px;width:100px;background:#f4f6fa;color:#3b5a98;border:1px solid #8fa0c4}
.content{left:138px;top:199px;width:706px;height:626px;background:var(--content-bg);border:1px solid var(--line)}
.content h2{position:absolute;left:57px;top:15px;font-size:24px;color:var(--heading)}
.bubble{position:absolute;left:22px;top:16px}
.rule{position:absolute;height:1px;background:#999}
.title{position:absolute;left:21px;top:94px;font-size:22px;font-weight:700;color:var(--accent-red)}
.banner{position:absolute;left:19px;top:138px;width:659px;height:176px;background:linear-gradient(#000 0,#000 55%,#2a2010 100%)}
.field{position:absolute;font-size:15px;display:flex}
.field b{color:var(--accent-red);width:94px;text-align:right;margin-right:16px;flex:none}
.desc-label{position:absolute;left:21px;top:476px;font-size:15px;font-weight:700;color:var(--accent-red)}
.desc{position:absolute;left:21px;top:502px;width:662px;font-size:12.5px;line-height:17.5px;text-indent:22px}
.read-more{position:absolute;left:586px;top:590px;width:102px;height:26px;background:var(--accent-red);color:#fff;font-size:13px;display:flex;align-items:center;justify-content:center}
.side{left:853px;width:210px;background:#fff;border:1px solid var(--line)}
.side-head{height:44px;background:#f3f3f3;border-bottom:1px solid #aaa;display:flex;align-items:center;gap:10px;padding-left:10px;font-size:17px;font-weight:700;color:var(--heading)}
.side ul{list-style:none}
.side li{height:37.5px;border-bottom:1px solid #b5b5b5;display:flex;align-items:center;padding-left:22px;font-size:13px}
.side li::before{content:"";width:7px;height:7px;background:var(--accent-red);margin-right:14px}
.side li:last-child{border-bottom:none}
</style>
</head>
<body>
<div class="abs page"></div>

<div class="abs logo"><span>BRIGHT HARBOR</span><span class="mark"></span></div>
<div class="abs btn-login">Login</div>
<div class="abs btn-register">Register</div>

<nav class="abs nav nav-main">
  <span>Home</span><span class="sep">|</span><span>About Us</span><span class="sep">|</span><span>Donate</span><span class="sep">|</span><span>Apply</span><span class="sep">|</span><span>Pledge</span><span class="sep">|</span><span>Nominate</span><span class="sep">|</span><span>Events</span><span class="sep">|</span><span>Contact Us</span><span class="sep">|</span><span>Directors</span>
</nav>

<section class="abs content">
  <svg class="bubble" width="26" height="28" viewBox="0 0 26 28"><ellipse cx="13" cy="11" rx="12" ry="10" fill="#111"/><path d="M6 18 L4 27 L13 20 Z" fill="#111"/></svg>
  <h2>Announcements</h2>
  <div class="rule" style="left:8px;top:57px;width:680px"></div>
  <div class="title">Harmony Day Information Sheet &amp; Booking Form</div>
  <div class="banner" role="img" aria-label="Harmony Day 24 March banner with a row of colourful figures holding hands"></div>
  <div class="field" style="left:-4px;top:344px"><b>Event Name:</b><span>Millbrook’s Inaugural Harmony Day Event 2012 Harmony Celebration Day<br>“EVERYONE BELONGS”</span></div>
  <div class="field" style="left:-8px;top:398px"><b>Date:</b><span>Saturday 24th March 2012</span></div>
  <div class="field" style="left:-8px;top:425px"><b>Venue:</b><span>Westvale Education Facilities, Ashford Road, Kellerton. Time: 10am – 3pm</span></div>
  <div class="rule" style="left:13px;top:462px;width:682px"></div>
  <div class="desc-label">Description:</div>
  <p class="desc">Harmony Day is celebrated around Australia on 21st March each year. It’s a day where all Australians celebrate our cultural diversity. The continuing message of Harmony,Harmony Day is celebrated around Australia on 21st March each year. It’s a day where all Australians celebrate our cultural diversity. The continuing message of Harmony...</p>
  <div class="read-more">Read More..</div>
</section>

<aside class="abs side" style="top:199px">
  <div class="side-head"><svg width="22" height="22" viewBox="0 0 22 22"><circle cx="11" cy="11" r="9.5" fill="none" stroke="#222" stroke-width="1.6"/><path d="M8 6 L15 11 L8 16" fill="none" stroke="#222" stroke-width="2"/></svg>Upcoming Events</div>
  <ul><li>Harmony Day</li><li>Harmony Day</li><li>Harmony Day</li><li>Harmony Day</li><li>Harmony Day</li><li>Harmony Day</li></ul>
</aside>

<aside class="abs side" style="top:496px">
  <div class="side-head"><svg width="22" height="22" viewBox="0 0 22 22"><circle cx="11" cy="11" r="9.5" fill="none" stroke="#222" stroke-width="1.6"/><path d="M8 6 L15 11 L8 16" fill="none" stroke="#222" stroke-width="2"/></svg>Sponsors</div>
  <ul><li>Harmony Day</li><li>Harmony Day</li><li>Harmony Day</li><li>Harmony Day</li><li>Harmony Day</li><li>Harmony Day</li></ul>
</aside>

<nav class="abs nav nav-foot">
  <span>Home</span><span class="sep">|</span><span>About Us</span><span class="sep">|</span><span>Donate</span><span class="sep">|</span><span>Apply</span><span class="sep">|</span><span>Pledge</span><span class="sep">|</span><span>Nominate</span><span class="sep">|</span><span>Events</span><span class="sep">|</span><span>Contact Us</span><span class="sep">|</span><span>Directors</span>
</nav>

<footer class="abs footer">
  <div class="abs copyright">Copyright © 2012 Bright Harbor Proprietary Limited.<br>All Rights Reserved</div>
  <div class="abs social chatter">Chatter</div>
  <div class="abs social friendbook">FriendBook</div>
</footer>
</body>
</html>
```